New travel store signage for Marlow Journeys to attract luxury travellers.

Hello,
We are looking to change the signage of our stores. The signage must include the following:
1. Marlow Journeys Logo (attached)
2. The text...The Travel & Cruise Experts
3. Brand Colours ( Fb0196, 412266, d41d84 and ffffff)
Please note the signage design must be central and only cover two thirds of the store front. We have also attached an image of one of our new stores which might be helpful when preparing a mock up.

We are looking for a quick turnaround on this, making a decision within 48 hours.

Target Market(s)

Retail

Industry/Entity Type

Travel Agency

Font styles to use
Other font styles liked:
• Radley

Colors
E54698
E96AAD
F1A4CE
F9D9EA
FCEFF6
6B429C
8869AF
B7A5CE
E3DAEB
F3F0F8

Requirements
Must have
• Hello, We are looking to change the signage of our stores. The signage must include the following: 1. Marlow Journeys Logo (attached) 2. The text...The Travel & Cruise Experts 3. Brand Colours ( Fb0196, 412266, d41d84 and ffffff) Please note the signage design must be central and only cover two thirds of the store front.
Should not have
• different colour or fonts. Gradient design.

```html
<!DOCTYPE html>
<html lang="en">
<head>
<meta charset="UTF-8">
<title>Marlow Journeys – Store Fascia Sign</title>
<link href="https://fonts.googleapis.com/css2?family=Radley&display=swap" rel="stylesheet">
<style>
  :root {
    --canvas-bg: #d9d9d9;
    --sign-white: #ffffff;
    --brand-pink: #d41d84;
    --brand-magenta: #c01a7a;
    --brand-plum: #5a1a5e;
    --brand-purple: #351a52;
    --brand-ink: #412266;
  }
  html, body {
    margin: 0;
    padding: 0;
    overflow: hidden;
  }
  body {
    width: 1200px;
    height: 919px;
    background: var(--canvas-bg);
    position: relative;
    font-family: "Radley", Georgia, serif;
  }
  .fascia-sign {
    position: absolute;
    left: 50px;
    top: 392px;
    width: 1100px;
    height: 135px;
    background: var(--sign-white);
  }
  .brand-panel {
    position: absolute;
    left: 0;
    top: 0;
    width: 252px;
    height: 100%;
    display: flex;
    align-items: center;
    justify-content: center;
    gap: 10px;
  }
  .brand-dot {
    width: 14px;
    height: 14px;
    border-radius: 50%;
    background: var(--brand-pink);
    flex: none;
  }
  .brand-name {
    font-family: "Radley", Georgia, serif;
    font-weight: 400;
    font-size: 27px;
    color: var(--brand-ink);
    white-space: nowrap;
  }
  .tagline-band {
    position: absolute;
    left: 252px;
    top: 0;
    width: 848px;
    height: 100%;
    background: linear-gradient(90deg,
      var(--brand-pink) 0%,
      var(--brand-magenta) 30%,
      var(--brand-plum) 62%,
      var(--brand-purple) 85%,
      var(--brand-purple) 100%);
    clip-path: polygon(0 50%, 33px 0, 100% 0, 100% 100%, 33px 100%);
    display: flex;
    align-items: center;
    justify-content: center;
    padding-left: 30px;
    box-sizing: border-box;
  }
  .tagline {
    margin: 0;
    font-family: "Radley", Georgia, serif;
    font-weight: 400;
    font-size: 62px;
    line-height: 1;
    color: var(--sign-white);
    white-space: nowrap;
  }
</style>
</head>
<body>
  <div class="fascia-sign">
    <div class="brand-panel">
      <span class="brand-dot"></span>
      <span class="brand-name">Marlow Journeys</span>
    </div>
    <div class="tagline-band">
      <p class="tagline">The Travel &amp; Cruise Experts</p>
    </div>
  </div>
</body>
</html>
```